Established research company needs fresh new powerpoint template

We need a powerpoint template for an established research and advisory company called Quenlow Partnership. We develop policy, improve delivery, and build capacity within the public sector - mainly in relation to education and young people.

We have a long and successful track record in our sector, and have a grown-up, clean brand. We already have a logo (see attached) and want a simple, clean powerpoint template that incorporates our logo and colours and matches the brand identity on our website: https://www.quenlowpartnership.com/

We need a title slide, a section header slide, a two-column slide for two panels of text, a two-column slide for one panel of text and one panel of imagery, and a single-column slide for text.

We want a template with built-in Styles so our team can make consistent-looking presentations without any manual formatting. We also want to use a font that will be compatible with devices used across a range of clients.

```html
<!DOCTYPE html>
<html lang="en">
<head>
<meta charset="utf-8">
<title>Quenlow Partnership – Presentation Template</title>
<link href="https://fonts.googleapis.com/css2?family=Montserrat:wght@800&family=Roboto:wght@400;500;700&display=swap" rel="stylesheet">
<style>
:root{
  --blue:#0d4a8a;
  --blue-light:#6aa3d1;
  --sky:#b9d4ea;
  --orange:#f07d32;
  --grey-bg:#f4f4f4;
  --ink:#333;
  --muted:#666;
  --white:#fff;
}
*{margin:0;padding:0;box-sizing:border-box}
html,body{width:1016px;height:1200px;overflow:hidden;background:var(--white)}
body{position:relative;font-family:"Roboto",Arial,sans-serif;color:var(--ink)}
.group-title{position:absolute;left:55px;font-family:"Montserrat",Arial,sans-serif;font-weight:800;font-size:38px;color:#1d4a8c;letter-spacing:.5px;line-height:1}
.slide{position:absolute;width:214px;height:120px;overflow:hidden;background:var(--white);box-shadow:0 7px 9px -3px rgba(0,0,0,.28)}
.slide > *{position:absolute}
.slide.grey{background:var(--grey-bg)}
.slide.blue{background:var(--blue);color:var(--white)}
.slide.sky{background:var(--sky)}
.c1{left:50px}.c2{left:284px}.c3{left:518px}.c4{left:753px}
.r0{top:147px}.r1{top:387px}.r2{top:545px}.r3{top:703px}.r4{top:861px}.r5{top:1018px}
.logo{font-weight:500;color:var(--blue);line-height:1;white-space:nowrap}
.blue .logo{color:var(--white)}
.logo-foot{left:4px;bottom:4px;font-size:4px;font-weight:500;color:var(--blue-light)}
.page-no{right:6px;bottom:3px;font-size:2px;color:#aaa}
.photo{background:linear-gradient(135deg,#3f73a8,#1d5590 55%,#6e95bd)}
.photo.warm{background:linear-gradient(160deg,#d98a6a,#c9524b 40%,#e9c29b 75%,#7aa36a)}
.photo.hammock{background:linear-gradient(180deg,#d7b08c,#b9835e 40%,#e2733a 70%,#6e5a4c)}
.photo.round{border-radius:50%}
.headline{font-weight:700;line-height:1.15}
.btn{background:var(--orange);color:var(--white);font-size:3.4px;border-radius:4px;padding:1.6px 5px;white-space:nowrap}
.url{font-size:3px;color:var(--white);white-space:nowrap}
.title{font-weight:500;color:var(--ink);line-height:1.1}
.blue .title{color:var(--white)}
.sub{font-size:3.3px;font-weight:700;color:var(--blue)}
.tiny{font-size:2.3px;line-height:2.9px;color:var(--muted)}
.blue .tiny{color:#dfe8f3}
.item{display:flex;gap:4px;align-items:flex-start}
.num{flex:none;width:10px;height:10px;border-radius:50%;background:var(--blue);color:var(--white);font-size:2.8px;display:flex;align-items:center;justify-content:center}
.num.light{background:var(--blue-light)}
.item-title{font-size:3.4px;font-weight:700;color:var(--blue);margin-top:1px}
.blue .item-title{color:var(--white)}
.item .tiny{margin-top:.6px}
.quote{width:78px;font-size:3.9px;font-weight:700;line-height:4.5px;color:var(--blue)}
.blue .quote{color:var(--white)}
.quote .mark{position:absolute;margin-left:-9px;font-size:9px;line-height:8px;font-family:Georgia,serif}
.quote .who{margin-top:6px;font-size:2.6px;line-height:3.4px;font-weight:400}
.quote .who b{font-weight:700;display:block;margin-bottom:.4px}
.vertical-name{transform:rotate(-90deg);transform-origin:left top;white-space:nowrap;font-weight:500;line-height:1}
.contact{display:flex;align-items:center;gap:6px;font-size:3.2px;color:var(--white)}
.contact svg{width:5px;height:5px}
</style>
</head>
<body>

<h1 class="group-title" style="top:80px">COVER SLIDES</h1>

<section class="slide c1 r0">
  <div class="logo" style="left:7px;top:8px;font-size:7.5px">Quenlow Partnership</div>
  <div class="photo" role="img" aria-label="Classroom of pupils raising their hands, blue tinted photograph" style="left:0;top:23px;width:214px;height:97px"></div>
  <p class="headline" style="left:26px;top:44px;width:150px;font-size:9.6px;color:var(--white)">We help the public sector solve problems and deliver effectively.</p>
  <span class="btn" style="left:25px;top:87px">Let's Start</span>
  <span class="url" style="left:26px;top:111px">www.quenlowpartnership.com</span>
</section>

<section class="slide c2 r0">
  <div class="logo" style="left:20px;top:20px;font-size:8px">Quenlow Partnership</div>
  <p class="headline" style="left:20px;top:48px;width:92px;font-size:7.8px;color:var(--blue)">We help the public sector solve problems and deliver effectively.</p>
  <span class="btn" style="left:19px;top:80px">Let's Start</span>
  <div class="photo round" role="img" aria-label="Classroom of pupils raising their hands, blue tinted photograph" style="left:114px;top:12px;width:90px;height:90px"></div>
  <div style="left:113px;top:112px;width:90px;height:8px;background:var(--blue)"></div>
  <span class="url" style="left:137px;top:114px">www.quenlowpartnership.com</span>
</section>

<section class="slide blue c3 r0">
  <div class="logo" style="left:62px;top:20px;font-size:10px">Quenlow Partnership</div>
  <p class="headline" style="left:62px;top:46px;width:100px;font-size:8.4px">We help the public sector solve problems and deliver effectively.</p>
  <span class="btn" style="left:62px;top:81px">Let's Start</span>
  <span class="url" style="left:62px;top:110px">www.quenlowpartnership.com</span>
</section>

<section class="slide blue c4 r0">
  <div class="logo" style="left:20px;top:18px;font-size:8.5px">Quenlow Partnership</div>
  <p class="headline" style="left:20px;top:48px;width:100px;font-size:8.4px">We help the public sector solve problems and deliver effectively.</p>
  <span class="btn" style="left:20px;top:80px">Let's Start</span>
  <span class="url" style="left:21px;top:111px">www.quenlowpartnership.com</span>
</section>

<h1 class="group-title" style="top:321px">CONTENT SLIDES</h1>

<section class="slide grey c1 r1">
  <div class="logo" style="left:14px;top:13px;font-size:8px">Quenlow Partnership</div>
  <h2 style="left:34px;top:44px;font-size:7.8px;font-weight:700;color:var(--blue)">INTRODUCTION</h2>
  <p style="left:34px;top:58px;width:125px;font-size:6.6px;line-height:8.6px;color:var(--ink)">We are a research and advisory company with a track-record in developing policy, improving delivery, and building capacity within the public sector.</p>
  <span class="page-no">1</span>
</section>

<section class="slide c2 r1">
  <div class="vertical-name" style="left:16px;top:115px;font-size:5.5px;color:var(--blue-light)">Quenlow Partnership</div>
  <h2 class="title" style="left:47px;top:16px;font-size:10px">What Will Cover Today</h2>
  <div class="item" style="left:45px;top:41px;width:78px"><span class="num">01</span><div><div class="item-title">Title Text Here</div><div class="tiny">Short supporting line for this point, kept brief.</div></div></div>
  <div class="item" style="left:45px;top:64px;width:78px"><span class="num">02</span><div><div class="item-title">Title Text Here</div><div class="tiny">Short supporting line for this point, kept brief.</div></div></div>
  <div class="item" style="left:45px;top:87px;width:78px"><span class="num">03</span><div><div class="item-title">Title Text Here</div><div class="tiny">Short supporting line for this point, kept brief.</div></div></div>
  <div class="item" style="left:126px;top:41px;width:78px"><span class="num">04</span><div><div class="item-title">Title Text Here</div><div class="tiny">Short supporting line for this point, kept brief.</div></div></div>
  <div class="item" style="left:126px;top:64px;width:78px"><span class="num">05</span><div><div class="item-title">Title Text Here</div><div class="tiny">Short supporting line for this point, kept brief.</div></div></div>
  <div class="item" style="left:126px;top:87px;width:78px"><span class="num">06</span><div><div class="item-title">Title Text Here</div><div class="tiny">Short supporting line for this point, kept brief.</div></div></div>
</section>

<section class="slide grey c3 r1">
  <div class="vertical-name" style="left:4px;top:116px;font-size:10px;color:#d6d9de">Quenlow Partnership</div>
  <h2 class="title" style="left:50px;top:16px;font-size:10px">What Will Cover Today</h2>
  <div class="item" style="left:48px;top:41px;width:76px"><span class="num">01</span><div><div class="item-title">Title Text Here</div><div class="tiny">Short supporting line for this point, kept brief.</div></div></div>
  <div class="item" style="left:48px;top:64px;width:76px"><span class="num">02</span><div><div class="item-title">Title Text Here</div><div class="tiny">Short supporting line for this point, kept brief.</div></div></div>
  <div class="item" style="left:48px;top:87px;width:76px"><span class="num">03</span><div><div class="item-title">Title Text Here</div><div class="tiny">Short supporting line for this point, kept brief.</div></div></div>
  <div class="item" style="left:128px;top:41px;width:78px"><span class="num">04</span><div><div class="item-title">Title Text Here</div><div class="tiny">Short supporting line for this point, kept brief.</div></div></div>
  <div class="item" style="left:128px;top:64px;width:78px"><span class="num">05</span><div><div class="item-title">Title Text Here</div><div class="tiny">Short supporting line for this point, kept brief.</div></div></div>
  <div class="item" style="left:128px;top:87px;width:78px"><span class="num">06</span><div><div class="item-title">Title Text Here</div><div class="tiny">Short supporting line for this point, kept brief.</div></div></div>
  <span class="page-no">7</span>
</section>

<section class="slide c4 r1">
  <h2 class="title" style="left:15px;top:11px;font-size:7px;font-weight:700">Your Title Text Goes Here</h2>
  <p style="left:15px;top:47px;width:78px;font-size:3.4px;line-height:4.2px;color:var(--muted)">We can support you to develop policies and strategies and design performance and delivery systems to implement these. We have a strong record in engaging stakeholders in designing systems and strategic planning.</p>
  <p style="left:108px;top:47px;width:78px;font-size:3.4px;line-height:4.2px;color:var(--muted)">We can support you to develop policies and strategies and design performance and delivery systems to implement these. We have a strong record in engaging stakeholders in designing systems and strategic planning.</p>
  <div class="logo-foot">Quenlow Partnership</div>
  <span class="page-no">8</span>
</section>

<section class="slide grey c1 r2">
  <h2 class="title" style="left:15px;top:11px;width:180px;font-size:6.8px;font-weight:700">Your Title Text Here Your Title Text Here Your Title Text Here Your Title Text Here</h2>
  <div class="sub" style="left:15px;top:35px">Title Text Here</div>
  <p class="tiny" style="left:15px;top:40px;width:78px">Body copy sits here in a clear, simple style so each team can share findings, set out next steps and keep every slide easy to read. Each paragraph uses the same size, weight and spacing, so decks stay tidy from the first page to the last, and anyone can add new points without changing any of the formatting by hand.</p>
  <div class="sub" style="left:113px;top:35px">Title Text Here</div>
  <p class="tiny" style="left:113px;top:40px;width:78px">Body copy sits here in a clear, simple style so each team can share findings, set out next steps and keep every slide easy to read. Each paragraph uses the same size, weight and spacing, so decks stay tidy from the first page to the last, and anyone can add new points without changing any of the formatting by hand.</p>
  <div class="sub" style="left:15px;top:72px">Title Text Here</div>
  <p class="tiny" style="left:15px;top:77px;width:78px">Body copy sits here in a clear, simple style so each team can share findings, set out next steps and keep every slide easy to read. Each paragraph uses the same size, weight and spacing, so decks stay tidy from the first page to the last, and anyone can add new points without changing any of the formatting by hand.</p>
  <div class="sub" style="left:113px;top:72px">Title Text Here</div>
  <p class="tiny" style="left:113px;top:77px;width:78px">Body copy sits here in a clear, simple style so each team can share findings, set out next steps and keep every slide easy to read. Each paragraph uses the same size, weight and spacing, so decks stay tidy from the first page to the last, and anyone can add new points without changing any of the formatting by hand.</p>
  <div class="logo-foot">Quenlow Partnership</div><span class="page-no">9</span>
</section>

<section class="slide grey c2 r2">
  <h2 class="title" style="left:15px;top:11px;width:180px;font-size:6.8px;font-weight:700">Your Title Text Here Your Title Text Here Your Title Text Here Your Title Text Here</h2>
  <div class="sub" style="left:15px;top:35px">Title Text Here</div>
  <p class="tiny" style="left:15px;top:40px;width:78px">Body copy sits here in a clear, simple style so each team can share findings, set out next steps and keep every slide easy to read. Each paragraph uses the same size, weight and spacing, so decks stay tidy from the first page to the last, and anyone can add new points without changing any of the formatting by hand.</p>
  <div class="sub" style="left:113px;top:35px">Title Text Here</div>
  <p class="tiny" style="left:113px;top:40px;width:78px">Body copy sits here in a clear, simple style so each team can share findings, set out next steps and keep every slide easy to read. Each paragraph uses the same size, weight and spacing, so decks stay tidy from the first page to the last, and anyone can add new points without changing any of the formatting by hand.</p>
  <div class="sub" style="left:15px;top:72px">Title Text Here</div>
  <p class="tiny" style="left:15px;top:77px;width:78px">Body copy sits here in a clear, simple style so each team can share findings, set out next steps and keep every slide easy to read. Each paragraph uses the same size, weight and spacing, so decks stay tidy from the first page to the last, and anyone can add new points without changing any of the formatting by hand.</p>
  <div class="sub" style="left:113px;top:72px">Title Text Here</div>
  <p class="tiny" style="left:113px;top:77px;width:78px">Body copy sits here in a clear, simple style so each team can share findings, set out next steps and keep every slide easy to read. Each paragraph uses the same size, weight and spacing, so decks stay tidy from the first page to the last, and anyone can add new points without changing any of the formatting by hand.</p>
  <div class="logo-foot">Quenlow Partnership</div><span class="page-no">10</span>
</section>

<section class="slide grey c3 r2">
  <h2 class="title" style="left:15px;top:11px;width:180px;font-size:6.8px;font-weight:700">Your Title Text Here Your Title Text Here Your Title Text Here Your Title Text Here</h2>
  <div class="sub" style="left:15px;top:35px">Title Text Here</div>
  <p class="tiny" style="left:15px;top:40px;width:78px">Body copy sits here in a clear, simple style so each team can share findings, set out next steps and keep every slide easy to read. Each paragraph uses the same size, weight and spacing, so decks stay tidy from the first page to the last, and anyone can add new points without changing any of the formatting by hand.</p>
  <p class="tiny" style="left:15px;top:66px;width:78px">Body copy sits here in a clear, simple style so each team can share findings, set out next steps and keep every slide easy to read. Each paragraph uses the same size, weight and spacing, so decks stay tidy from the first page to the last, and anyone can add new points without changing any of the formatting by hand.</p>
  <div class="sub" style="left:113px;top:35px">Title Text Here</div>
  <p class="tiny" style="left:113px;top:40px;width:78px">Body copy sits here in a clear, simple style so each team can share findings, set out next steps and keep every slide easy to read. Each paragraph uses the same size, weight and spacing, so decks stay tidy from the first page to the last, and anyone can add new points without changing any of the formatting by hand.</p>
  <p class="tiny" style="left:113px;top:66px;width:78px">Body copy sits here in a clear, simple style so each team can share findings, set out next steps and keep every slide easy to read. Each paragraph uses the same size, weight and spacing, so decks stay tidy from the first page to the last, and anyone can add new points without changing any of the formatting by hand.</p>
  <div class="logo-foot">Quenlow Partnership</div><span class="page-no">11</span>
</section>

<section class="slide grey c4 r2">
  <h2 class="title" style="left:15px;top:11px;width:180px;font-size:6.8px;font-weight:700">Your Title Text Here Your Title Text Here Your Title Text Here Your Title Text Here</h2>
  <div class="sub" style="left:15px;top:35px">Title Text Here</div>
  <p class="tiny" style="left:15px;top:40px;width:78px">Body copy sits here in a clear, simple style so each team can share findings, set out next steps and keep every slide easy to read. Each paragraph uses the same size, weight and spacing, so decks stay tidy from the first page to the last, and anyone can add new points without changing any of the formatting by hand.</p>
  <p class="tiny" style="left:15px;top:66px;width:78px">Body copy sits here in a clear, simple style so each team can share findings, set out next steps and keep every slide easy to read. Each paragraph uses the same size, weight and spacing, so decks stay tidy from the first page to the last, and anyone can add new points without changing any of the formatting by hand.</p>
  <div class="sub" style="left:113px;top:35px">Title Text Here</div>
  <p class="tiny" style="left:113px;top:40px;width:78px">Body copy sits here in a clear, simple style so each team can share findings, set out next steps and keep every slide easy to read. Each paragraph uses the same size, weight and spacing, so decks stay tidy from the first page to the last, and anyone can add new points without changing any of the formatting by hand.</p>
  <p class="tiny" style="left:113px;top:66px;width:78px">Body copy sits here in a clear, simple style so each team can share findings, set out next steps and keep every slide easy to read. Each paragraph uses the same size, weight and spacing, so decks stay tidy from the first page to the last, and anyone can add new points without changing any of the formatting by hand.</p>
  <div class="logo-foot">Quenlow Partnership</div><span class="page-no">12</span>
</section>

<section class="slide blue c1 r3">
  <div class="vertical-name" style="left:34px;top:110px;font-size:6px;color:var(--blue-light)">Quenlow Partnership</div>
  <h2 class="headline" style="left:75px;top:50px;font-size:10px">Section Divider<br>Title Here</h2>
</section>

<section class="slide blue c2 r3">
  <div style="left:-40px;top:-58px;width:106px;height:101px;border-radius:50%;background:var(--blue-light)"></div>
  <div class="logo" style="left:8px;top:10px;font-size:7.5px">Quenlow Partnership</div>
  <h2 class="headline" style="left:70px;top:58px;font-size:10px">Section Divider<br>Title Here</h2>
</section>

<section class="slide c3 r3">
  <div class="photo warm" role="img" aria-label="Group of cheerful children in red caps with arms raised outdoors" style="left:0;top:0;width:103px;height:111px"></div>
  <h2 class="title" style="left:109px;top:11px;font-size:7px;font-weight:700">Title Text Here</h2>
  <p class="tiny" style="left:109px;top:20px;width:92px">A short note on this step and how it helps the work move forward with care, written in plain words so the point is clear and quick to take in.</p>
  <div class="item" style="left:109px;top:42px;width:94px"><span class="num light">01</span><p class="tiny">A short note on this step and how it helps the work move forward with care, written in plain words so the point is clear and quick to take in.</p></div>
  <div class="item" style="left:109px;top:62px;width:94px"><span class="num light">02</span><p class="tiny">A short note on this step and how it helps the work move forward with care, written in plain words so the point is clear and quick to take in.</p></div>
  <div class="item" style="left:109px;top:82px;width:94px"><span class="num light">03</span><p class="tiny">A short note on this step and how it helps the work move forward with care, written in plain words so the point is clear and quick to take in.</p></div>
  <div class="logo-foot">Quenlow Partnership</div><span class="page-no">13</span>
</section>

<section class="slide c4 r3">
  <h2 class="title" style="left:15px;top:11px;font-size:7px;font-weight:700">Title Text Here</h2>
  <p class="tiny" style="left:15px;top:20px;width:90px">A short note on this step and how it helps the work move forward with care, written in plain words so the point is clear and quick to take in.</p>
  <div class="item" style="left:15px;top:40px;width:92px"><span class="num light">01</span><p class="tiny">A short note on this step and how it helps the work move forward with care, written in plain words so the point is clear and quick to take in.</p></div>
  <div class="item" style="left:15px;top:60px;width:92px"><span class="num light">02</span><p class="tiny">A short note on this step and how it helps the work move forward with care, written in plain words so the point is clear and quick to take in.</p></div>
  <div class="item" style="left:15px;top:80px;width:92px"><span class="num light">03</span><p class="tiny">A short note on this step and how it helps the work move forward with care, written in plain words so the point is clear and quick to take in.</p></div>
  <div class="photo warm" role="img" aria-label="Group of cheerful children in red caps with arms raised outdoors" style="left:114px;top:0;width:100px;height:108px"></div>
  <div class="logo-foot">Quenlow Partnership</div><span class="page-no">14</span>
</section>

<section class="slide c1 r4">
  <div class="photo hammock" role="img" aria-label="Two girls relaxing together in an orange hammock" style="left:0;top:0;width:214px;height:60px"></div>
  <h2 class="title" style="left:15px;top:11px;font-size:7px;color:var(--white)">Title Text here</h2>
  <div class="item" style="left:13px;top:70px;width:60px"><span class="num">01</span><div><div class="item-title">Title Text Here</div><p class="tiny">A short note on this step and how it helps the work move forward with care, written in plain words so the point is clear and quick to take in.</p></div></div>
  <div class="item" style="left:76px;top:70px;width:60px"><span class="num">02</span><div><div class="item-title">Title Text Here</div><p class="tiny">A short note on this step and how it helps the work move forward with care, written in plain words so the point is clear and quick to take in.</p></div></div>
  <div class="item" style="left:139px;top:70px;width:60px"><span class="num">03</span><div><div class="item-title">Title Text Here</div><p class="tiny">A short note on this step and how it helps the work move forward with care, written in plain words so the point is clear and quick to take in.</p></div></div>
  <div class="logo-foot">Quenlow Partnership</div><span class="page-no">17</span>
</section>

<section class="slide c2 r4">
  <div class="photo warm round" role="img" aria-label="Group of cheerful children in red caps with arms raised outdoors" style="left:13px;top:15px;width:86px;height:86px"></div>
  <div style="left:68px;top:61px;width:32px;height:32px;border-radius:50%;background:var(--blue-light)"></div>
  <h2 class="title" style="left:113px;top:16px;font-size:7px;font-weight:700">Title Text Here</h2>
  <div class="item" style="left:113px;top:33px;width:90px"><span class="num light" style="width:9px;height:9px"></span><div><div class="item-title" style="color:var(--blue-light)">Title Text Here</div><p class="tiny">Short supporting line for this point, kept brief.</p></div></div>
  <div class="item" style="left:113px;top:56px;width:90px"><span class="num light" style="width:9px;height:9px"></span><div><div class="item-title" style="color:var(--blue-light)">Title Text Here</div><p class="tiny">Short supporting line for this point, kept brief.</p></div></div>
  <div class="item" style="left:113px;top:79px;width:90px"><span class="num light" style="width:9px;height:9px"></span><div><div class="item-title" style="color:var(--blue-light)">Title Text Here</div><p class="tiny">Short supporting line for this point, kept brief.</p></div></div>
  <div class="logo-foot">Quenlow Partnership</div><span class="page-no">18</span>
</section>

<section class="slide blue c3 r4">
  <div class="photo warm round" role="img" aria-label="Group of cheerful children in red caps with arms raised outdoors" style="left:13px;top:15px;width:86px;height:86px"></div>
  <div style="left:68px;top:61px;width:32px;height:32px;border-radius:50%;background:var(--blue-light)"></div>
  <h2 class="title" style="left:113px;top:16px;font-size:7px;font-weight:700">Title Text Here</h2>
  <div class="item" style="left:113px;top:33px;width:90px"><span class="num light" style="width:9px;height:9px"></span><div><div class="item-title">Title Text Here</div><p class="tiny">Short supporting line for this point, kept brief.</p></div></div>
  <div class="item" style="left:113px;top:56px;width:90px"><span class="num light" style="width:9px;height:9px"></span><div><div class="item-title">Title Text Here</div><p class="tiny">Short supporting line for this point, kept brief.</p></div></div>
  <div class="item" style="left:113px;top:79px;width:90px"><span class="num light" style="width:9px;height:9px"></span><div><div class="item-title">Title Text Here</div><p class="tiny">Short supporting line for this point, kept brief.</p></div></div>
  <div class="logo-foot" style="color:#cfe0f0">Quenlow Partnership</div>
</section>

<section class="slide sky c4 r4">
  <blockquote class="quote" style="left:26px;top:24px"><span class="mark">“</span>Mutual respect and clarity of purpose were embodied in the approach undertaken by Quenlow Partnership … at the closure of their involvement, we felt in a strong position to construct a detailed action plan to move us forward with purpose and clarity, thanks to the skill and expertise that Quenlow brought to the process.”<div class="who"><b>MAREN THWAITE,</b>HEAD OF CHILDREN AND YOUNG PEOPLE'S SPECIALIST SERVICES, NORTHVALE COUNTY COUNCIL</div></blockquote>
  <blockquote class="quote" style="left:116px;top:24px"><span class="mark">“</span>Mutual respect and clarity of purpose were embodied in the approach undertaken by Quenlow Partnership … at the closure of their involvement, we felt in a strong position to construct a detailed action plan to move us forward with purpose and clarity, thanks to the skill and expertise that Quenlow brought to the process.”<div class="who"><b>MAREN THWAITE,</b>HEAD OF CHILDREN AND YOUNG PEOPLE'S SPECIALIST SERVICES, NORTHVALE COUNTY COUNCIL</div></blockquote>
  <div class="logo-foot" style="color:#8fb6d8">Quenlow Partnership</div>
</section>

<section class="slide blue c1 r5">
  <blockquote class="quote" style="left:26px;top:24px"><span class="mark">“</span>Mutual respect and clarity of purpose were embodied in the approach undertaken by Quenlow Partnership … at the closure of their involvement, we felt in a strong position to construct a detailed action plan to move us forward with purpose and clarity, thanks to the skill and expertise that Quenlow brought to the process.”<div class="who"><b>MAREN THWAITE,</b>HEAD OF CHILDREN AND YOUNG PEOPLE'S SPECIALIST SERVICES, NORTHVALE COUNTY COUNCIL</div></blockquote>
  <blockquote class="quote" style="left:116px;top:24px"><span class="mark">“</span>Mutual respect and clarity of purpose were embodied in the approach undertaken by Quenlow Partnership … at the closure of their involvement, we felt in a strong position to construct a detailed action plan to move us forward with purpose and clarity, thanks to the skill and expertise that Quenlow brought to the process.”<div class="who"><b>MAREN THWAITE,</b>HEAD OF CHILDREN AND YOUNG PEOPLE'S SPECIALIST SERVICES, NORTHVALE COUNTY COUNCIL</div></blockquote>
  <div class="logo-foot" style="color:#cfe0f0">Quenlow Partnership</div>
</section>

<section class="slide c2 r5">
  <div style="left:0;top:0;width:214px;height:36px;background:var(--blue)"></div>
  <h2 class="title" style="left:15px;top:11px;width:180px;font-size:6.8px;font-weight:700;color:var(--white)">Title Text Here Title Text Here Title Text Here Title Text Here</h2>
  <div class="sub" style="left:15px;top:40px">Title Text Here</div>
  <p class="tiny" style="left:15px;top:45px;width:78px">Body copy sits here in a clear, simple style so each team can share findings, set out next steps and keep every slide easy to read. Each paragraph uses the same size, weight and spacing, so decks stay tidy from the first page to the last, and anyone can add new points without changing any of the formatting by hand.</p>
  <div class="sub" style="left:113px;top:40px">Title Text Here</div>
  <p class="tiny" style="left:113px;top:45px;width:78px">Body copy sits here in a clear, simple style so each team can share findings, set out next steps and keep every slide easy to read. Each paragraph uses the same size, weight and spacing, so decks stay tidy from the first page to the last, and anyone can add new points without changing any of the formatting by hand.</p>
  <div class="sub" style="left:15px;top:78px">Title Text Here</div>
  <p class="tiny" style="left:15px;top:83px;width:78px">Body copy sits here in a clear, simple style so each team can share findings, set out next steps and keep every slide easy to read. Each paragraph uses the same size, weight and spacing, so decks stay tidy from the first page to the last, and anyone can add new points without changing any of the formatting by hand.</p>
  <div class="sub" style="left:113px;top:78px">Title Text Here</div>
  <p class="tiny" style="left:113px;top:83px;width:78px">Body copy sits here in a clear, simple style so each team can share findings, set out next steps and keep every slide easy to read. Each paragraph uses the same size, weight and spacing, so decks stay tidy from the first page to the last, and anyone can add new points without changing any of the formatting by hand.</p>
  <div class="logo-foot">Quenlow Partnership</div><span class="page-no">22</span>
</section>

<section class="slide c3 r5">
  <div style="left:0;top:0;width:84px;height:120px;background:var(--blue)"></div>
  <h2 class="title" style="left:15px;top:11px;font-size:6.8px;font-weight:700;color:var(--white)">Title Text Here<br>Title Text Here<br>Title Text Here<br>Title Text Here</h2>
  <p class="tiny" style="left:102px;top:19px;width:97px;color:var(--ink)">A short note on this step and how it helps the work move forward with care, written in plain words so the point is clear and quick to take in.</p>
  <div class="item" style="left:100px;top:44px;width:100px"><span class="num">01</span><p class="tiny">A short note on this step and how it helps the work move forward with care, written in plain words so the point is clear and quick to take in.</p></div>
  <div class="item" style="left:100px;top:64px;width:100px"><span class="num">02</span><p class="tiny">A short note on this step and how it helps the work move forward with care, written in plain words so the point is clear and quick to take in.</p></div>
  <div class="item" style="left:100px;top:84px;width:100px"><span class="num">03</span><p class="tiny">A short note on this step and how it helps the work move forward with care, written in plain words so the point is clear and quick to take in.</p></div>
  <div class="logo-foot" style="color:#cfe0f0">Quenlow Partnership</div><span class="page-no">23</span>
</section>

<section class="slide blue c4 r5">
  <div class="photo round" role="img" aria-label="Classroom of pupils raising their hands, blue tinted photograph" style="left:16px;top:16px;width:89px;height:89px;background:linear-gradient(135deg,#6f9cc9,#3a6ea4 60%,#8cb0d4)"></div>
  <div style="left:15px;top:116px;width:103px;height:4px;background:var(--blue-light)"></div>
  <div class="logo" style="left:117px;top:24px;font-size:7.5px">Quenlow Partnership</div>
  <h2 class="headline" style="left:117px;top:44px;font-size:10px">Get In Touch</h2>
  <div class="contact" style="left:117px;top:60px"><svg viewBox="0 0 24 24" fill="#cfe0f0"><path d="M6.6 10.8a15 15 0 0 0 6.6 6.6l2.2-2.2a1 1 0 0 1 1-.25 11.4 11.4 0 0 0 3.6.57 1 1 0 0 1 1 1V20a1 1 0 0 1-1 1A17 17 0 0 1 3 4a1 1 0 0 1 1-1h3.5a1 1 0 0 1 1 1c0 1.250.2 2.450.57 3.570a1 1 0 0 1-.25 1z"/></svg>123 456 789</div>
  <div class="contact" style="left:117px;top:71px"><svg viewBox="0 0 24 24" fill="#cfe0f0"><path d="M2 5h20v14H2z M2 5l10 8 10-8" stroke="#0d4a8a" stroke-width="1.5"/></svg>name@quenlowpartnership.com</div>
  <div class="contact" style="left:117px;top:82px"><svg viewBox="0 0 24 24" fill="none" stroke="#cfe0f0" stroke-width="2.5"><circle cx="12" cy="12" r="9"/><path d="M3 12h18M12 3c3 3 3 15 0 18M12 3c-3 3-3 15 0 18"/></svg>www.quenlowpartnership.com</div>
</section>

</body>
</html>
```